Velmarotix - world unique technology for better life - please let them know who am i at first sight

We need a new business card for company which is a provider of unique crystal based technology suitable for all living being. For more information and final design you can use our brochure (our colours are black and blue from brochure).
We use Verdana font

Industry/Entity Type

Business

Contact Information for Business Card

regular dimension

Font styles to use
Other font styles liked:
• Verdana

Requirements
Must have
• Logo
• name
• function/position
• phone
• mobile
• e-mail
• adress
Nice to have
• inovative design (technology directed)

```html
<!DOCTYPE html>
<html lang="en">
<head>
<meta charset="utf-8">
<title>Velmarotix business card</title>
<link href="https://fonts.googleapis.com/css2?family=Open+Sans:wght@300;400;600&display=swap" rel="stylesheet">
<style>
  :root {
    --bg: #ecedef;
    --paper: #ffffff;
    --paper-shade: #f1f2f3;
    --blue: #29b6e3;
    --blue-deep: #1a9fd0;
    --blue-light: #7fd3ef;
    --blue-pale: #bfe8f6;
    --ink-light: #ffffff;
  }
  * { box-sizing: border-box; margin: 0; padding: 0; }
  html, body { width: 1200px; height: 858px; overflow: hidden; }
  body {
    background: var(--bg);
    font-family: "Open Sans", Verdana, sans-serif;
    display: flex;
    align-items: center;
    justify-content: center;
    gap: 48px;
  }
  .card {
    width: 520px;
    height: 300px;
    border-radius: 4px;
    overflow: hidden;
    position: relative;
    box-shadow: 0 10px 28px rgba(0,0,0,0.14);
  }

  /* Front */
  .card-front { background: var(--paper); display: flex; flex-direction: column; }
  .front-brand {
    height: 118px;
    background: linear-gradient(180deg, var(--paper), var(--paper-shade));
    display: flex;
    align-items: center;
    padding-left: 36px;
    gap: 16px;
  }
  .brand-dot {
    width: 56px; height: 56px; border-radius: 50%;
    background: var(--blue-light);
    flex: none;
  }
  .brand-name {
    font-weight: 300;
    font-size: 44px;
    letter-spacing: 2px;
    color: var(--blue);
    text-transform: uppercase;
  }
  .front-info {
    flex: 1;
    background: linear-gradient(160deg, var(--blue) 0%, var(--blue-deep) 100%);
    color: var(--ink-light);
    display: flex;
    align-items: center;
    padding: 0 30px 0 36px;
  }
  .person { flex: 1; }
  .person-name { font-size: 22px; font-weight: 600; line-height: 1.1; }
  .person-role { font-size: 14px; font-weight: 400; margin-top: 2px; }
  .person-address { font-size: 12.5px; font-weight: 400; margin-top: 18px; line-height: 1.45; }
  .divider { width: 1px; height: 118px; background: rgba(255,255,255,0.7); margin: 0 22px; }
  .contacts { list-style: none; font-size: 13px; line-height: 1; }
  .contacts li { display: flex; align-items: center; gap: 10px; margin: 8px 0; }
  .contacts svg { width: 14px; height: 14px; flex: none; }

  /* Back */
  .card-back {
    background: radial-gradient(circle at 35% 45%, var(--blue-pale) 0%, var(--blue-light) 45%, var(--blue) 100%);
    display: flex;
    align-items: center;
    justify-content: center;
  }
  .back-texture {
    position: absolute; inset: 0;
    background: radial-gradient(ellipse at 75% 55%, rgba(255,255,255,0.22) 0%, rgba(255,255,255,0) 60%);
  }
  .back-brand { position: relative; display: flex; align-items: center; gap: 18px; }
  .back-brand .brand-dot { background: rgba(255,255,255,0.75); width: 64px; height: 64px; }
  .back-brand .brand-name { color: var(--ink-light); font-size: 46px; }
</style>
</head>
<body>

<section class="card card-front">
  <header class="front-brand">
    <span class="brand-dot"></span>
    <span class="brand-name">Velmarotix</span>
  </header>
  <div class="front-info">
    <div class="person">
      <p class="person-name">Employee Name</p>
      <p class="person-role">Employee Position</p>
      <p class="person-address">28 Harrow Lane<br>London N7 3QX, United Kingdom</p>
    </div>
    <span class="divider"></span>
    <ul class="contacts">
      <li>
        <svg viewBox="0 0 14 14" aria-hidden="true"><rect x="4" y="1" width="6" height="12" rx="1" fill="none" stroke="#fff" stroke-width="1.3"/><circle cx="7" cy="11" r="0.8" fill="#fff"/></svg>
        + xxx(x) xx xxx xxx
      </li>
      <li>
        <svg viewBox="0 0 14 14" aria-hidden="true"><path d="M3 2h2.5l1 3-1.5 1a7 7 0 0 0 3 3l1-1.5 3 1V11a1.5 1.5 0 0 1-1.5 1.5A9.5 9.5 0 0 1 1.5 3.5 1.5 1.5 0 0 1 3 2z" fill="#fff"/></svg>
        +385(0) 51 402 937
      </li>
      <li>
        <svg viewBox="0 0 14 14" aria-hidden="true"><rect x="1" y="3" width="12" height="8" fill="none" stroke="#fff" stroke-width="1.3"/><path d="M1 3l6 5 6-5" fill="none" stroke="#fff" stroke-width="1.3"/></svg>
        info@velmarotix.eu
      </li>
      <li>
        <svg viewBox="0 0 14 14" aria-hidden="true"><circle cx="7" cy="7" r="5.5" fill="none" stroke="#fff" stroke-width="1.3"/><path d="M1.5 7h11M7 1.5c-3 3.5-3 7.5 0 11M7 1.5c3 3.5 3 7.5 0 11" fill="none" stroke="#fff" stroke-width="1"/></svg>
        www.velmarotix.eu
      </li>
    </ul>
  </div>
</section>

<section class="card card-back">
  <div class="back-texture" role="img" aria-label="Soft pattern of scattered light blue crystal facets"></div>
  <div class="back-brand">
    <span class="brand-dot"></span>
    <span class="brand-name">Velmarotix</span>
  </div>
</section>

</body>
</html>
```